Pitch Deck Powerpoint Template for Entrepreneurship/Education Based Nonprofit

I need a stylish powerpoint design for a start-up nonprofit called Harbor Venture Works (HVW). I am building HVWs pitch deck to raise money. HVW is an entrepreneurial incubator and accelerator that seeks to identify, validate, test, and launch innovative ventures that improve public education. An example of our model, and one of our partners, is Kestrel Schools in New Orleans and New York :http://kestrelsch.example.org

We need the deck to look sleek and innovative - like a start-up pitch deck. Lots of different templates and fonts that pop off the page.

Target Market(s)

Individuals, foundations, and any other stakeholder - we are pitching a new business model and asking for money.

Industry/Entity Type

Building

Font styles to use
Sans Serif

Requirements
Must have
• A sleek/modern feel with several different template slides. charts and graphs/ strong fonts that pop off the page, use of the logo:
• It would be great to have a slide describing the 3 primary programs at Harbor Venture Works (HVW):
• - HVWspark - come in with an idea for an innovation in education, and we will do a two day workshop to examine your business assumptions and discuss next steps.
• - HVWpropell - take your idea to a prototype and launch to customers - we help you with an intensive 30 day program
• - HVWnurture - for existing nonprofit projects, we allow you to work under our umbrella to launch and build capacity
• Slides: Problem Definition, Solution, Value Proposition, Data/MEasurement, Key Partners, About the founder, Key Advisors

```html
<!DOCTYPE html>
<html lang="en">
<head>
<meta charset="utf-8">
<title>Alabama Slide – Harbor Venture Works</title>
<link href="https://fonts.googleapis.com/css2?family=Oswald:wght@400;500&family=Source+Sans+3:ital,wght@0,400;0,600;0,700;1,400&display=swap" rel="stylesheet">
<style>
  :root{
    --board:#000000;
    --paper:#ffffff;
    --navy:#00447c;
    --heading-blue:#1a4d80;
    --ink:#111111;
    --rule:#cfcfcf;
    --purple:#6b2c91;
    --green:#5a8a1a;
    --orange:#f15a29;
    --sky:#29a8e0;
    --magenta:#a6218e;
    --quote-grey:#7a7a7a;
    --page-num:#2a5bd7;
  }
  *{margin:0;padding:0;box-sizing:border-box}
  html,body{width:1200px;height:1200px;overflow:hidden;background:var(--board)}
  .board{position:relative;width:1200px;height:1200px;background:var(--board);font-family:"Source Sans 3",sans-serif}
  .board-title{position:absolute;top:72px;left:0;width:1200px;text-align:center;color:#fff;font-size:32px;font-weight:400;letter-spacing:.5px}
  .board-number{position:absolute;right:38px;bottom:22px;color:var(--page-num);font-size:24px;font-weight:700}
  .slide{position:absolute;left:35px;top:168px;width:1128px;height:845px;background:var(--paper);overflow:hidden}
  .title-bar{position:absolute;left:0;top:47px;width:808px;height:104px;background:var(--navy)}
  .title-bar h1{position:absolute;left:37px;top:22px;font-family:"Oswald",sans-serif;font-weight:500;font-size:48px;color:#fff;letter-spacing:.5px}
  .brand{position:absolute;left:838px;top:44px;display:flex;align-items:center;gap:10px}
  .brand-dot{width:18px;height:18px;border-radius:50%;background:var(--magenta);flex:none}
  .brand-name{font-family:"Source Sans 3",sans-serif;font-weight:700;font-size:34px;line-height:34px;color:var(--navy)}
  .rule-v{position:absolute;left:443px;top:182px;width:1px;height:520px;background:var(--rule)}
  .rule-h{position:absolute;left:36px;top:430px;width:836px;height:1px;background:var(--rule)}
  .point{position:absolute;width:345px}
  .point .num{position:absolute;left:-58px;top:-1px;width:46px;height:46px;border-radius:50%;color:#fff;font-family:"Oswald",sans-serif;font-size:24px;line-height:46px;text-align:center}
  .point h2{font-family:"Oswald",sans-serif;font-weight:400;font-size:36px;line-height:44px;letter-spacing:-.3px}
  .point h3{margin-top:4px;font-weight:600;font-size:28px;line-height:32px;color:var(--heading-blue);letter-spacing:.5px}
  .point p{margin-top:4px;font-size:19px;line-height:25px;color:var(--ink);text-align:justify}
  .p1{left:89px;top:185px}.p2{left:522px;top:185px}.p3{left:89px;top:484px}.p4{left:522px;top:484px}
  .p1 .num{background:var(--purple)}.p1 h2{color:var(--purple)}
  .p2 .num{background:var(--green)}.p2 h2{color:var(--green)}
  .p3 .num{background:var(--orange)}.p3 h2{color:var(--orange)}
  .p4 .num{background:var(--sky)}.p4 h2{color:var(--sky)}
  .state-map{position:absolute;left:913px;top:190px;width:167px;height:257px;background:var(--navy);border-radius:6px}
  .quote{position:absolute;left:895px;top:490px;width:212px;height:210px}
  .quote .mark{position:absolute;font-family:"Oswald",sans-serif;font-size:64px;line-height:64px;color:var(--quote-grey);font-weight:500}
  .quote .open{left:0;top:-4px}
  .quote .close{right:0;bottom:-30px}
  .quote p{position:absolute;left:20px;top:12px;width:160px;text-align:center;font-style:italic;font-size:19px;line-height:25px;color:var(--magenta)}
  .footer-wave{position:absolute;left:0;top:743px;width:1128px;height:22px}
  .footer{position:absolute;left:0;top:762px;width:1128px;height:83px;background:var(--magenta);color:#fff;font-weight:700;font-size:27px}
  .footer .page{position:absolute;left:50px;top:25px}
  .footer .url{position:absolute;right:58px;top:25px}
</style>
</head>
<body>
<div class="board">
  <div class="board-title">ALABAMA SLIDE</div>

  <section class="slide">
    <header class="title-bar"><h1>ALABAMA</h1></header>
    <div class="brand">
      <span class="brand-dot"></span>
      <span class="brand-name">Harbor Venture<br>Works</span>
    </div>

    <div class="rule-v"></div>
    <div class="rule-h"></div>

    <article class="point p1">
      <span class="num">1</span>
      <h2>PROBLEM</h2>
      <h3>SOLUTION</h3>
      <p>Lorem ipsum dolor sit amet, consectetuer adipiscing elit, sed diam nonummy nibh euismod tincidunt ut laoreet dolore magna aliquam erat volutpat.</p>
    </article>
    <article class="point p2">
      <span class="num">2</span>
      <h2>PROBLEM</h2>
      <h3>SOLUTION</h3>
      <p>Lorem ipsum dolor sit amet, consectetuer adipiscing elit, sed diam nonummy nibh euismod tincidunt ut laoreet dolore magna aliquam erat volutpat.</p>
    </article>
    <article class="point p3">
      <span class="num">3</span>
      <h2>PROBLEM</h2>
      <h3>SOLUTION</h3>
      <p>Lorem ipsum dolor sit amet, consectetuer adipiscing elit, sed diam nonummy nibh euismod tincidunt ut laoreet dolore magna aliquam erat volutpat.</p>
    </article>
    <article class="point p4">
      <span class="num">4</span>
      <h2>PROBLEM</h2>
      <h3>SOLUTION</h3>
      <p>Lorem ipsum dolor sit amet, consectetuer adipiscing elit, sed diam nonummy nibh euismod tincidunt ut laoreet dolore magna aliquam erat volutpat.</p>
    </article>

    <div class="state-map" role="img" aria-label="Map silhouette of the state of Alabama in navy"></div>

    <blockquote class="quote">
      <span class="mark open">“</span>
      <p>Lorem ipsum dolor sit amet, consectetuer adipisc sing elit, sed diam nonummy nib serat volutpat.</p>
      <span class="mark close">”</span>
    </blockquote>

    <svg class="footer-wave" viewBox="0 0 1128 22" preserveAspectRatio="none" aria-hidden="true">
      <defs>
        <pattern id="scallop" width="23.5" height="22" patternUnits="userSpaceOnUse">
          <path d="M0 12 Q5.9 2 11.75 12 T23.5 12 V22 H0 Z" fill="#a6218e"/>
          <path d="M0 12 Q5.9 2 11.75 12 T23.5 12" fill="none" stroke="#00447c" stroke-width="4"/>
        </pattern>
      </defs>
      <rect width="1128" height="22" fill="url(#scallop)"/>
    </svg>
    <footer class="footer">
      <span class="page">Page 1</span>
      <span class="url">www.hvw.example.com</span>
    </footer>
  </section>

  <div class="board-number">24</div>
</div>
</body>
</html>
```